Brookmere Osteopathy flyer

I want a clean clear DL flyer (but also want an A4 poster) promoting a new Osteopathic business in a semi rural area in Tasmania (Australia).
It can have pictures like the examples attached to show people what Osteopathy is (its like Chiropractic and physiotherapy).
I am the sole practioner and am male, so any pictures would be best to be a white male if possible.
I've attached some wording, you can use all, or none of it
I don't have a phone number for the business yet
info@brookmereosteopathy.example
www.brookmereosteopathy.example
Target Market(s)
Australians, from tradies, professionals, babies to retired people
Industry/Entity Type
Health
Look and feel

```html
<!DOCTYPE html>
<html lang="en">
<head>
<meta charset="utf-8">
<title>Brookmere Osteopathy Flyer</title>
<link href="https://fonts.googleapis.com/css2?family=Montserrat:wght@700;800;900&family=Barlow+Condensed:wght@500&family=Bebas+Neue&display=swap" rel="stylesheet">
<style>
  :root{
    --blue:#1a8fd6;
    --orange:#f7903a;
    --ink:#333537;
    --paper:#ffffff;
    --stage:#eef1f3;
    --photo-light:#e8eef2;
    --photo-skin:#e9cdb8;
  }
  *{margin:0;padding:0;box-sizing:border-box}
  html,body{width:1200px;height:1200px;overflow:hidden;background:var(--stage)}
  .stage{position:relative;width:1200px;height:1200px}
  .flyer{
    position:absolute;left:300px;top:0;width:836px;height:1672px;
    transform:scale(0.7177);transform-origin:top left;
    background:var(--paper);overflow:hidden;
    font-family:"Montserrat",sans-serif;color:var(--ink);
  }
  .abs{position:absolute}
  .brand-mark{left:66px;top:56px;width:304px;height:304px;border:3px solid var(--blue);border-radius:50%;
    display:flex;align-items:center;justify-content:center;text-align:center}
  .brand-name{font-weight:800;color:var(--blue);font-size:30px;line-height:1.2;letter-spacing:1px}
  .headline{left:415px;top:52px;font-weight:900;font-size:84px;line-height:72px;letter-spacing:-1px}
  .headline .blue{color:var(--blue)} .headline .orange{color:var(--orange)}
  .subhead{left:418px;top:353px;font-weight:800;font-size:31px;line-height:33px;color:var(--ink)}
  .hero-photo{left:0;top:388px;width:480px;height:420px}
  .round-photo{border-radius:50%;border:2px solid var(--blue);background:var(--paper);padding:14px}
  .round-photo span{display:block;width:100%;height:100%;border-radius:50%;
    background:radial-gradient(circle at 60% 40%,var(--photo-skin),var(--photo-light) 70%)}
  .reasons-title{left:63px;top:858px;font-weight:800;font-size:31px;line-height:31px;color:var(--blue)}
  .reasons-title .orange{color:var(--orange)}
  .reason-list{list-style:none;font-family:"Barlow Condensed",sans-serif;font-weight:500;font-size:27px;color:var(--ink);white-space:nowrap}
  .reason-list li{display:flex;align-items:center;height:37.5px}
  .reason-list svg{width:20px;height:20px;margin-right:8px;flex:none}
  .approach-box{left:62px;top:1174px;width:712px;height:148px;border:2px solid var(--blue);border-radius:12px}
  .approach-tab{left:68px;top:-2px;width:580px;height:40px;background:var(--blue);color:#fff;
    font-weight:800;font-size:24px;display:flex;align-items:center;justify-content:center;border-radius:0 0 26px 26px}
  .approach-cols{position:absolute;left:0;right:0;top:56px;display:flex}
  .approach-cols div{flex:1;text-align:center;font-weight:800;font-size:17.5px;line-height:19px;padding:6px 6px;border-left:1.5px solid #bbb}
  .approach-cols div:first-child{border-left:none}
  .cta{left:72px;top:1344px;font-family:"Bebas Neue",sans-serif;font-size:46px;line-height:41px;color:var(--blue)}
  .cta .orange{color:var(--orange)}
  .phone{left:322px;top:1330px;font-family:"Bebas Neue",sans-serif;font-size:122px;line-height:110px;color:var(--orange);letter-spacing:-1px}
  .email{left:326px;top:1442px;font-weight:800;font-size:20px;display:flex;align-items:center;gap:10px;white-space:nowrap}
  .address-tab{left:100px;top:1488px;width:636px;height:62px;background:var(--blue);border-radius:18px 18px 0 0;
    color:#fff;font-weight:800;font-size:31px;text-align:center;padding-top:8px;white-space:nowrap}
  .web-pill{left:62px;top:1540px;width:712px;height:88px;background:var(--orange);border:3px solid var(--blue);border-radius:44px;
    color:#fff;font-weight:800;font-size:29px;display:flex;align-items:center;justify-content:center;white-space:nowrap}
</style>
</head>
<body>
<div class="stage">
  <div class="flyer">
    <div class="abs brand-mark"><div class="brand-name">BROOKMERE<br>OSTEOPATHY</div></div>

    <div class="abs headline">
      <div class="blue">FEEL</div><div class="orange">BETTER</div><div class="blue">MOVE</div><div class="orange">FREELY</div>
    </div>
    <div class="abs subhead">OSTEOPATHY<br>HELPS EASE PAIN &amp;<br>RESTORE MOBILITY.</div>

    <svg class="abs hero-photo" viewBox="0 0 480 420" role="img" aria-label="Photo of a practitioner treating a man's neck and upper back">
      <defs><linearGradient id="heroFill" x1="0" y1="0" x2="1" y2="1">
        <stop offset="0" stop-color="#f2f4f6"/><stop offset="0.55" stop-color="#7cc4e6"/><stop offset="1" stop-color="#3aa6dc"/></linearGradient></defs>
      <path d="M0 0 H300 Q470 80 470 250 L430 330 Q250 330 30 400 L0 400 Z" fill="url(#heroFill)"/>
      <path d="M40 440 Q200 330 360 380" fill="none" stroke="var(--orange)" stroke-width="34" stroke-linecap="round"/>
    </svg>

    <div class="abs round-photo" style="left:474px;top:475px;width:300px;height:300px" role="img" aria-label="Photo of a man receiving neck treatment"><span></span></div>
    <div class="abs round-photo" style="left:337px;top:613px;width:244px;height:244px" role="img" aria-label="Photo of a woman lying down during head and neck treatment"><span></span></div>
    <div class="abs round-photo" style="left:500px;top:745px;width:256px;height:256px" role="img" aria-label="Photo of a woman receiving jaw and head treatment"><span></span></div>

    <div class="abs reasons-title">COMMON REASONS<br>PEOPLE VISIT<br><span class="orange">AN OSTEOPATH:</span></div>

    <ul class="abs reason-list" style="left:63px;top:965px">
      <li><svg viewBox="0 0 20 20"><circle cx="10" cy="10" r="8" fill="none" stroke="var(--orange)" stroke-width="1.6"/><path d="M6 10.2l2.8 2.6L14 7.4" fill="none" stroke="var(--orange)" stroke-width="1.8"/></svg>Back / neck pain</li>
      <li><svg viewBox="0 0 20 20"><circle cx="10" cy="10" r="8" fill="none" stroke="var(--orange)" stroke-width="1.6"/><path d="M6 10.2l2.8 2.6L14 7.4" fill="none" stroke="var(--orange)" stroke-width="1.8"/></svg>Headaches / migraines</li>
      <li><svg viewBox="0 0 20 20"><circle cx="10" cy="10" r="8" fill="none" stroke="var(--orange)" stroke-width="1.6"/><path d="M6 10.2l2.8 2.6L14 7.4" fill="none" stroke="var(--orange)" stroke-width="1.8"/></svg>Joint and muscle pain</li>
      <li><svg viewBox="0 0 20 20"><circle cx="10" cy="10" r="8" fill="none" stroke="var(--orange)" stroke-width="1.6"/><path d="M6 10.2l2.8 2.6L14 7.4" fill="none" stroke="var(--orange)" stroke-width="1.8"/></svg>Pregnancy-related discomfort</li>
      <li><svg viewBox="0 0 20 20"><circle cx="10" cy="10" r="8" fill="none" stroke="var(--orange)" stroke-width="1.6"/><path d="M6 10.2l2.8 2.6L14 7.4" fill="none" stroke="var(--orange)" stroke-width="1.8"/></svg>Disc related issues</li>
    </ul>
    <ul class="abs reason-list" style="left:403px;top:965px">
      <li><svg viewBox="0 0 20 20"><circle cx="10" cy="10" r="8" fill="none" stroke="var(--orange)" stroke-width="1.6"/><path d="M6 10.2l2.8 2.6L14 7.4" fill="none" stroke="var(--orange)" stroke-width="1.8"/></svg>Sciatica</li>
      <li><svg viewBox="0 0 20 20"><circle cx="10" cy="10" r="8" fill="none" stroke="var(--orange)" stroke-width="1.6"/><path d="M6 10.2l2.8 2.6L14 7.4" fill="none" stroke="var(--orange)" stroke-width="1.8"/></svg>Plantar fasciitis</li>
      <li><svg viewBox="0 0 20 20"><circle cx="10" cy="10" r="8" fill="none" stroke="var(--orange)" stroke-width="1.6"/><path d="M6 10.2l2.8 2.6L14 7.4" fill="none" stroke="var(--orange)" stroke-width="1.8"/></svg>Tendonitis / Bursitis</li>
      <li><svg viewBox="0 0 20 20"><circle cx="10" cy="10" r="8" fill="none" stroke="var(--orange)" stroke-width="1.6"/><path d="M6 10.2l2.8 2.6L14 7.4" fill="none" stroke="var(--orange)" stroke-width="1.8"/></svg>Adhesive capsulitis (frozen shoulder)</li>
      <li><svg viewBox="0 0 20 20"><circle cx="10" cy="10" r="8" fill="none" stroke="var(--orange)" stroke-width="1.6"/><path d="M6 10.2l2.8 2.6L14 7.4" fill="none" stroke="var(--orange)" stroke-width="1.8"/></svg>Tennis / Golfers elbow</li>
    </ul>

    <div class="abs approach-box">
      <div class="abs approach-tab">OSTEOPATHS USE A COMBINATION OF</div>
      <div class="approach-cols">
        <div>RELIEVE PAIN,<br>RESTORE<br>MOVEMENT.</div>
        <div>MOVE<br>BETTER,<br>FEEL BETTER.</div>
        <div>PAIN RELIEF.<br>NATURAL<br>MOVEMENT.</div>
        <div>OSTEOPATHY<br>FOR PAIN &amp;<br>MOBILITY.</div>
      </div>
    </div>

    <div class="abs cta">CONTACT TODAY<br>TO BOOK YOUR<br><span class="orange">APPOINTMENT</span></div>
    <div class="abs phone">9805551234</div>
    <div class="abs email">
      <svg width="22" height="16" viewBox="0 0 24 18"><rect x="1" y="1" width="22" height="16" fill="var(--blue)"/><path d="M1 1l11 9 11-9" fill="none" stroke="#fff" stroke-width="1.8"/></svg>
      info@brookmereosteopathy.example
    </div>

    <div class="abs address-tab">24 Mill Creek road, Brookmere</div>
    <div class="abs web-pill">www.brookmereosteopathy.example</div>
  </div>
</div>
</body>
</html>
```